Real Estate Company / Capital Needs Cards!

need business cards designed using the logos that were just designed by pixelbarn.

Reason: per designers request deadline extended 1 day…thank you.

Target Market(s)

Investors and clients looking to purchase real estate or invest in the business.

Industry/Entity Type

Business

Requirements
Must have
• two designs - one for the real estate logo and one for the capital logo, similar but slightly different.
Nice to have
• something to make it pop (perhaps on the back)
Should not have
• much color

```html
<!DOCTYPE html>
<html lang="en">
<head>
<meta charset="utf-8">
<title>Maren Real Estate – Business Cards</title>
<link rel="stylesheet" href="https://fonts.googleapis.com/css2?family=Open+Sans:wght@400;600;700&display=swap">
<style>
  :root {
    --backdrop: #e9e7e4;
    --card-white: #ffffff;
    --panel-grey: #6d6e71;
    --arc-grey: #8f9194;
    --mark-grey: #7b7c7f;
    --text-light: #ffffff;
    --text-dark: #3a3a3c;
  }
  * { box-sizing: border-box; margin: 0; padding: 0; }
  html, body { width: 1200px; height: 498px; overflow: hidden; }
  body {
    background: var(--backdrop);
    font-family: "Open Sans", Arial, sans-serif;
    position: relative;
  }
  .card {
    position: absolute;
    top: 99px;
    width: 500px;
    height: 300px;
    background: var(--card-white);
    box-shadow: 0 3px 10px rgba(0,0,0,0.18);
    overflow: hidden;
  }
  .card--front { left: 70px; }
  .card--back { left: 630px; }

  .front-shape { position: absolute; inset: 0; }

  .brand {
    position: absolute;
    left: 44px;
    top: 126px;
    display: flex;
    align-items: center;
    gap: 10px;
    color: var(--mark-grey);
    font-weight: 600;
  }
  .brand__square {
    width: 34px; height: 34px;
    background: var(--mark-grey);
    border-radius: 4px;
  }
  .brand__name { font-size: 17px; letter-spacing: 2px; line-height: 1.15; text-transform: uppercase; }

  .contact {
    position: absolute;
    right: 16px;
    top: 22px;
    text-align: right;
    color: var(--text-light);
    white-space: nowrap;
  }
  .contact__name { font-size: 18px; font-weight: 700; line-height: 1.1; }
  .contact__title { font-size: 15px; font-weight: 400; margin-bottom: 44px; }
  .contact__line {
    font-size: 13px;
    line-height: 22px;
    display: flex;
    justify-content: flex-end;
    align-items: center;
    gap: 4px;
  }
  .contact__icon { width: 11px; height: 11px; fill: var(--text-light); flex: none; }
  .contact__address { font-size: 13px; line-height: 20px; margin-top: 26px; }

  .back-brand {
    position: absolute;
    left: 0; right: 0;
    top: 96px;
    display: flex;
    flex-direction: column;
    align-items: center;
    gap: 14px;
    color: var(--mark-grey);
    font-weight: 600;
  }
  .back-brand__square {
    width: 92px; height: 92px;
    background: var(--mark-grey);
    border-radius: 12px;
  }
  .back-brand__name { font-size: 20px; letter-spacing: 3px; text-transform: uppercase; }
  .website {
    position: absolute;
    left: 0; right: 0;
    bottom: 40px;
    text-align: center;
    font-size: 15px;
    letter-spacing: 3px;
    color: var(--text-dark);
  }
  .website strong { font-weight: 700; }
</style>
</head>
<body>

<section class="card card--front" aria-label="Business card front">
  <svg class="front-shape" viewBox="0 0 500 300" width="500" height="300" aria-hidden="true">
    <path d="M258 0 C305 90 310 210 280 300 L500 300 L500 0 Z" fill="var(--panel-grey)"/>
    <path d="M240 0 C290 90 295 210 264 300" fill="none" stroke="var(--arc-grey)" stroke-width="5"/>
  </svg>

  <div class="brand">
    <span class="brand__square"></span>
    <span class="brand__name">Maren<br>Real Estate</span>
  </div>

  <div class="contact">
    <p class="contact__name">Your Name</p>
    <p class="contact__title">Title</p>
    <p class="contact__line">
      <svg class="contact__icon" viewBox="0 0 12 12"><path d="M2.5 0.8 L4.6 3 L3.6 4.3 C4.3 5.8 6 7.6 7.6 8.3 L8.9 7.3 L11.2 9.4 L9.8 11.2 C5.5 10.8 1 6.3 0.8 2.2 Z"/></svg>
      <span>123-456-7980</span>
    </p>
    <p class="contact__line">
      <svg class="contact__icon" viewBox="0 0 12 12"><rect x="3" y="1" width="6" height="4"/><rect x="1" y="5" width="10" height="5" rx="1"/></svg>
      <span>123-568-7896</span>
    </p>
    <p class="contact__line">
      <svg class="contact__icon" viewBox="0 0 12 12"><rect x="0.5" y="2.5" width="11" height="7.5" rx="1"/><path d="M1 3 L6 7 L11 3" fill="none" stroke="var(--panel-grey)" stroke-width="1.2"/></svg>
      <span>marenrealestate@mail.com</span>
    </p>
    <p class="contact__address">Street Name City Name<br>State ZipCode</p>
  </div>
</section>

<section class="card card--back" aria-label="Business card back">
  <div class="back-brand">
    <span class="back-brand__square"></span>
    <span class="back-brand__name">Maren Real Estate</span>
  </div>
  <p class="website">www.<strong>marenrealestate</strong>.com</p>
</section>

</body>
</html>
```